Veterinary Pylon

My veterinary clinic is not clearly visible from the street and I want to place a Pylon next to my driveway. I want a modern, elegant straight Design, the Photo shows the sheduled place. One can see the clinic on our Homepage: www.tailbright-vethaus.at
The last pictures are examples for pylones I like

Target Market(s)

the passing cars often miss my entry...I want to show where to turn left

Colors
3276b5
33a6d7
00a990

Requirements
Must have
• High value, simple elegance, size: 250cm (high) x 100cm (width)
Nice to have
• Our Logo, arrow(?)

A special Text is not necessary but this will be an option:

Biegen sie hier ab und wir biegen es wieder hin!
Should not have
• Too much Color, the colors I have chosen are the possible colors but it‘s not necessary to use them.

```html
<!DOCTYPE html>
<html lang="de">
<head>
<meta charset="utf-8">
<title>Tailbright Vethaus – Pylon</title>
<link rel="stylesheet" href="https://fonts.googleapis.com/css2?family=Montserrat:wght@700&display=swap">
<style>
  :root {
    --backdrop: #eef0f3;
    --pylon-blue: #2a4a8c;
    --post-steel: #a9adb3;
    --post-shade: #7d8288;
    --text-white: #ffffff;
    --photo-light: #d9dde3;
    --photo-mid: #8a7f78;
    --photo-dark: #3b2c26;
  }
  * { margin: 0; padding: 0; box-sizing: border-box; }
  html, body { width: 818px; height: 1200px; overflow: hidden; background: var(--backdrop); }
  .canvas { position: relative; width: 818px; height: 1200px; font-family: "Montserrat", sans-serif; font-weight: 700; color: var(--text-white); }
  .pylon-shape { position: absolute; left: 0; top: 0; }
  .brand {
    position: absolute; left: 0; width: 818px; top: 405px; text-align: center; line-height: 1;
  }
  .brand-name { display: block; font-size: 50px; letter-spacing: 1px; }
  .brand-sub { display: block; font-size: 26px; letter-spacing: 12px; margin-top: 16px; padding-left: 12px; }
  .slogan {
    position: absolute; left: 256px; top: 702px; width: 340px;
    font-size: 36px; line-height: 42px; letter-spacing: -0.2px;
  }
  .photo-area {
    position: absolute; left: 257px; top: 846px; width: 298px; height: 168px;
    background: linear-gradient(160deg, var(--photo-light) 0%, var(--photo-mid) 55%, var(--photo-dark) 100%);
  }
  .website {
    position: absolute; left: 257px; top: 1038px; width: 310px;
    font-size: 19.5px; letter-spacing: 0.1px;
  }
</style>
</head>
<body>
<div class="canvas">
  <svg class="pylon-shape" width="818" height="1200" viewBox="0 0 818 1200" aria-hidden="true">
    <defs>
      <mask id="panel-cut">
        <rect x="0" y="0" width="818" height="1200" fill="#fff"/>
        <circle cx="409" cy="387" r="293" fill="#000"/>
      </mask>
    </defs>
    <g class="posts">
      <rect x="298" y="620" width="36" height="80" fill="var(--post-steel)"/>
      <rect x="322" y="620" width="12" height="80" fill="var(--post-shade)"/>
      <rect x="484" y="620" width="36" height="80" fill="var(--post-steel)"/>
      <rect x="508" y="620" width="12" height="80" fill="var(--post-shade)"/>
    </g>
    <rect class="info-panel" x="209" y="600" width="400" height="515" fill="var(--pylon-blue)" mask="url(#panel-cut)"/>
    <circle class="logo-disc" cx="409" cy="387" r="267" fill="var(--pylon-blue)"/>
    <circle class="brand-ring" cx="409" cy="285" r="78" fill="none" stroke="var(--text-white)" stroke-width="7"/>
  </svg>

  <div class="brand">
    <span class="brand-name">TAILBRIGHT</span>
    <span class="brand-sub">VETHAUS</span>
  </div>

  <p class="slogan">Biegen Sie ein, dann biegen wir es hin!</p>

  <div class="photo-area" role="img" aria-label="Foto: Tierärztin untersucht einen braunen Hund per Ultraschall auf einem roten Behandlungstisch"></div>

  <p class="website">www.tailbright-vethaus.at</p>
</div>
</body>
</html>
```